Corvane Business Cards

Front of business card will have logo, name, address, & telephone number. Back of card will have a list of services provided - Roads, Substation Pads, Temporary Pads, Site Pads, Land Leveling, Powerline Row Cleaning, Land Clearing, Gates, Fencing, Construction Entrances, Excavation, Trenching, Underground Utilities, Directional Boring, Pile Driving. We are a construction company that uses heavy equipment like bulldozers, motor graders/blades, dump trucks, backhoes, hydro axes, & skid loaders. We build roads, pads, & install electric utility lines & waterlines underground. This logo is new. The word "Construction" can be smaller as uploaded 2 example edited logos. We will be using this card design for many employees.
Target Market(s)
Industrial Electric Powerline, Wind Turbine, Solar Panel, & Water Utility companies.
Contact Information for Business Card
Name/Position - Dwayne Halster - Owner
Address: 4875 FM 309
Dalbrook, TX 79412
Phone number - (325) 482-5096

```html
<!DOCTYPE html>
<html lang="en">
<head>
<meta charset="utf-8">
<title>Corvane Construction Business Cards</title>
<link href="https://fonts.googleapis.com/css2?family=Roboto:wght@300;400;500&display=swap" rel="stylesheet">
<style>
  :root {
    --backdrop: #e6e6e6;
    --card: #2e2e2e;
    --card-edge: #6a1f2c;
    --ink: #f2f2f2;
    --ink-soft: #c9c9c9;
    --emboss: #4a4a4a;
    --rule: #d8d8d8;
  }
  * { box-sizing: border-box; margin: 0; padding: 0; }
  html, body {
    width: 1200px; height: 801px; overflow: hidden;
    background: var(--backdrop);
    font-family: "Roboto", Arial, sans-serif;
  }
  .sheet {
    width: 1200px; height: 801px;
    display: flex; align-items: center; justify-content: center; gap: 44px;
  }
  .card {
    position: relative;
    width: 530px; height: 303px;
    background: var(--card);
    border-bottom: 2px solid var(--card-edge);
    border-right: 2px solid var(--card-edge);
    color: var(--ink);
    overflow: hidden;
  }
  /* front */
  .brand {
    position: absolute; top: 52px; left: 0; right: 0;
    display: flex; align-items: center; justify-content: center; gap: 12px;
  }
  .brand-dot { width: 14px; height: 14px; border-radius: 50%; background: var(--ink); }
  .brand-name {
    font-weight: 400; font-size: 27px; letter-spacing: 2px; color: var(--ink);
    white-space: nowrap;
  }
  .divider {
    position: absolute; left: 40px; right: 40px; top: 150px;
    height: 1px; background: var(--rule);
  }
  .person { position: absolute; left: 40px; top: 168px; }
  .person-name { font-size: 21px; font-weight: 500; }
  .person-role { font-size: 12px; font-weight: 300; color: var(--ink-soft); margin-top: 2px; }
  .contacts { position: absolute; left: 40px; bottom: 28px; list-style: none; }
  .contacts li {
    display: flex; align-items: center; gap: 9px;
    font-size: 13px; font-weight: 300; line-height: 20px; white-space: nowrap;
  }
  .contacts svg { width: 11px; height: 11px; fill: var(--ink); }
  .address {
    position: absolute; right: 40px; top: 168px; text-align: right;
    font-size: 13px; font-weight: 300; line-height: 19px; white-space: nowrap;
  }
  /* back */
  .brand-large {
    position: absolute; top: 62px; left: 0; right: 0; text-align: center;
    font-size: 33px; font-weight: 400; letter-spacing: 2px; color: var(--emboss);
    white-space: nowrap;
  }
  .services {
    position: absolute; left: 20px; right: 20px; top: 140px;
    text-align: center; font-size: 15px; font-weight: 300; line-height: 23px;
    color: var(--ink); white-space: nowrap;
  }
</style>
</head>
<body>
<main class="sheet">
  <section class="card card-front" aria-label="Front of business card">
    <div class="brand">
      <span class="brand-dot"></span>
      <span class="brand-name">CORVANE CONSTRUCTION</span>
    </div>
    <div class="divider"></div>
    <div class="person">
      <p class="person-name">Dwayne Halster</p>
      <p class="person-role">Owner</p>
    </div>
    <ul class="contacts">
      <li><svg viewBox="0 0 24 24"><path d="M6.6 10.8a15 15 0 0 0 6.6 6.6l2.2-2.2a1 1 0 0 1 1-.25 11.4 11.4 0 0 0 3.6.57 1 1 0 0 1 1 1V20a1 1 0 0 1-1 1A17 17 0 0 1 3 4a1 1 0 0 1 1-1h3.5a1 1 0 0 1 1 1c0 1.25.2 2.45.57 3.57a1 1 0 0 1-.25 1z"/></svg>(325) 482-5096</li>
      <li><svg viewBox="0 0 24 24"><path d="M2 5h20v14H2zm2 2v.5l8 5 8-5V7zm0 2.8V17h16V9.8l-8 5z"/></svg>Dwayne@corvaneconstruction.com</li>
      <li><svg viewBox="0 0 24 24"><circle cx="12" cy="12" r="10"/></svg>www.corvaneconstruction.com</li>
    </ul>
    <p class="address">4875 FM 309<br>Dalbrook, TX 79412</p>
  </section>

  <section class="card card-back" aria-label="Back of business card">
    <p class="brand-large">CORVANE CONSTRUCTION</p>
    <p class="services">
      provided • Roads • Substation Pads • Temporary Pads • Site Pads<br>
      Land Leveling • Powerline Row Cleaning • Land Clearing • Gates<br>
      Fencing • Construction Entrances • Excavation • Trenching<br>
      Underground Utilities • Directional Boring • Pile Driving
    </p>
  </section>
</main>
</body>
</html>
```